Simple Logo Design for Semi-Clear Plastic Frosted Card stock

Create a business card on frosted plastic. compliment existing logo elements with a tree trunk, roots, or seed at the lower half and the full logo both on the front.

Contact information will go on a solid portion of the back of this design since this card stock is semi-transparent.

It is important to consider this plastic card stock medium in your design. I found helpful tips and guides listed at vellaprint-sample.net: be careful to understand ink printed on plastic cards cannot have too much of a consistent print area or risks peeling and fine lines can easily scratch off.
Updates

2" x 3.5" 20PT Clear Plastic Business cards with Round corners Please get info or templates here: https://www.vellaprint-sample.net/product-detail/2-x-35-20pt-clear-plastic-business-cards-with-round-corners

Target Market(s)

Not for profit- religion

Industry/Entity Type

Business

Must include complementary elements to the existing logo

Font styles to use
Decorative

Colors
000000

Requirements
Must have
• Elements of community, nature and oneness. Such as: seed, roots, tree trunk, etc.
• Three lines of space on the back for Name, Title, Phone Number.
Nice to have
• I like a light use of decorative elements
Should not have
• No eyes, from faces or animals.

```html
<!DOCTYPE html>
<html lang="en">
<head>
<meta charset="utf-8">
<title>Steadfast Path – Business Card</title>
<link href="https://fonts.googleapis.com/css2?family=Open+Sans:wght@400;600;700&display=swap" rel="stylesheet">
<style>
  :root {
    --page-bg: #d9d6d1;
    --card-frost-top: #eef0ed;
    --card-frost-bottom: #dfe3df;
    --card-edge: rgba(255,255,255,0.7);
    --brand-teal: #1f4d48;
    --brand-green: #3f7b2c;
    --band-teal: #1d4a44;
    --band-green: #2f6a2a;
    --ink: #1b1b1b;
    --leaf-light: rgba(120,150,110,0.18);
    --leaf-deep: rgba(90,125,85,0.28);
  }
  * { margin: 0; padding: 0; box-sizing: border-box; }
  html, body {
    width: 1200px;
    height: 969px;
    overflow: hidden;
    background: var(--page-bg);
    font-family: "Open Sans", Arial, sans-serif;
  }
  .canvas {
    position: relative;
    width: 1200px;
    height: 969px;
  }
  .card {
    position: absolute;
    left: 100px;
    top: 199px;
    width: 1000px;
    height: 571px;
    border-radius: 22px;
    overflow: hidden;
    background: linear-gradient(180deg, var(--card-frost-top), var(--card-frost-bottom));
    border: 1px solid var(--card-edge);
  }
  .leaf-art {
    position: absolute;
    left: 545px;
    top: 31px;
    width: 455px;
    height: 500px;
    border-radius: 46% 40% 30% 50%;
    background: radial-gradient(ellipse at 55% 45%, var(--leaf-deep), var(--leaf-light) 60%, transparent 80%);
  }
  .brand-mark {
    position: absolute;
    left: 190px;
    top: 72px;
    width: 110px;
    height: 110px;
    border-radius: 50%;
    background: var(--brand-teal);
  }
  .brand-name {
    position: absolute;
    left: 64px;
    top: 196px;
    font-size: 40px;
    font-weight: 700;
    letter-spacing: 0.5px;
    color: var(--brand-teal);
    white-space: nowrap;
  }
  .brand-tagline {
    position: absolute;
    left: 100px;
    top: 244px;
    font-size: 15px;
    font-weight: 600;
    letter-spacing: 0.4px;
    color: var(--brand-teal);
    text-transform: uppercase;
    white-space: nowrap;
  }
  .contact-name {
    position: absolute;
    left: 68px;
    top: 374px;
    font-size: 36px;
    font-weight: 700;
    letter-spacing: 1px;
    color: var(--brand-teal);
  }
  .contact-title {
    position: absolute;
    left: 68px;
    top: 424px;
    font-size: 28px;
    font-weight: 400;
    letter-spacing: 1px;
    color: var(--brand-green);
  }
  .contact-rule {
    position: absolute;
    left: 242px;
    top: 455px;
    width: 689px;
    height: 2px;
    background: var(--brand-teal);
  }
  .contact-phone {
    position: absolute;
    right: 69px;
    top: 416px;
    font-size: 30px;
    font-weight: 400;
    letter-spacing: 1px;
    color: var(--ink);
  }
  .base-band {
    position: absolute;
    left: 0;
    bottom: 0;
    width: 1000px;
    height: 40px;
  }
</style>
</head>
<body>
<div class="canvas">
  <div class="card">
    <div class="leaf-art" role="img" aria-label="Faint illustration of a leafy sprouting branch"></div>

    <div class="brand-mark"></div>
    <div class="brand-name">STEADFAST PATH</div>
    <div class="brand-tagline">Wisdom, Fellowship &amp; Calm</div>

    <div class="contact-name">MARCUS HALE</div>
    <div class="contact-title">PRESIDENT</div>
    <div class="contact-rule"></div>
    <div class="contact-phone">555 0142 7781</div>

    <svg class="base-band" viewBox="0 0 1000 40" preserveAspectRatio="none" aria-hidden="true">
      <polygon points="0,0 665,0 645,40 0,40" fill="var(--band-teal)"/>
      <polygon points="670,0 1000,0 1000,40 650,40" fill="var(--band-green)"/>
    </svg>
  </div>
</div>
</body>
</html>
```